first fantastic look and impression

We are looking for a concept for letterhead, business card, emailfooter and template for invoices or offers for our company in the consultation business.
The dancer is a symbol who we are: it looks simple, but there is a lot of hard work and many years of training in this movement. The look is also what we want: elegant, modern, strong, with a touch of extravaganza
Target Market(s)
Hotelbusiness , Consulting
Font styles to use
Sans Serif
Other font styles liked:
- please give us a option we are open
Requirements
Must have
- We are not typical consultants but sparring partners and coaches for the hotel and that should also be expressed in the design. Maybe there is an icon that supports the whole thing. We are more modern and bolder than our industry colleagues.
we are modern, fresh, agile, fast
Nice to have
- a icon

```html
<!DOCTYPE html>
<html lang="en">
<head>
<meta charset="utf-8">
<title>Veltin Consulting Letterhead</title>
<link href="https://fonts.googleapis.com/css2?family=Open+Sans:wght@400;600;700&display=swap" rel="stylesheet">
<style>
  :root {
    --backdrop: #dfe3e5;
    --paper: #ffffff;
    --brand-blue: #5f7f9f;
    --brand-gold: #e2c27f;
    --rule-grey: #7d8288;
    --text-grey: #6a7079;
    --watermark: #eef0f2;
  }
  * { margin: 0; padding: 0; box-sizing: border-box; }
  html, body {
    width: 1200px; height: 784px; overflow: hidden;
    background: var(--backdrop);
    font-family: "Open Sans", Arial, sans-serif;
  }
  .letterhead {
    position: absolute; left: 340px; top: 22px;
    width: 520px; height: 740px;
    background: var(--paper);
    box-shadow: 0 6px 20px rgba(60, 70, 80, 0.18);
    overflow: hidden;
  }
  .brand {
    position: absolute; left: 34px; top: 34px;
    display: flex; align-items: center; gap: 8px;
  }
  .brand-square { width: 10px; height: 10px; background: var(--brand-blue); }
  .brand-name {
    font-size: 19px; font-weight: 400; color: var(--brand-blue);
    letter-spacing: 0.3px; line-height: 1;
  }
  .header-rule {
    position: absolute; left: 34px; top: 72px; width: 446px; height: 1.5px;
    background: var(--rule-grey);
  }
  .header-rule::after {
    content: ""; position: absolute; right: -6px; top: -3px;
    width: 7px; height: 7px; background: var(--brand-blue);
  }
  .contact {
    position: absolute; right: 34px; top: 82px;
    font-size: 7.5px; line-height: 1.6; color: var(--text-grey);
    font-style: normal; font-weight: 400;
  }
  .contact-line { display: flex; align-items: center; gap: 4px; white-space: nowrap; }
  .contact-city { color: var(--brand-blue); font-weight: 700; }
  .contact-line svg { width: 8px; height: 8px; flex: none; }
  .contact-web { margin-left: 10px; display: inline-flex; align-items: center; gap: 4px; }
  .watermark {
    position: absolute; left: 110px; top: 260px;
    width: 240px; height: 210px;
    background: radial-gradient(ellipse at 50% 50%, var(--watermark) 0%, rgba(238,240,242,0.6) 55%, rgba(255,255,255,0) 75%);
  }
  .footer-bands { position: absolute; left: 0; bottom: 0; width: 100%; height: 16px; }
</style>
</head>
<body>
  <main class="letterhead">
    <div class="brand">
      <span class="brand-square"></span>
      <span class="brand-name">Veltin Consulting</span>
    </div>
    <div class="header-rule"></div>
    <address class="contact">
      <div class="contact-line contact-city">
        <svg viewBox="0 0 8 8"><circle cx="4" cy="4" r="4" fill="#5f7f9f"/><circle cx="4" cy="3.4" r="1.3" fill="#fff"/></svg>
        Lindenau/Austria
      </div>
      <div class="contact-line">
        <svg viewBox="0 0 8 8"><circle cx="4" cy="4" r="4" fill="#5f7f9f"/><rect x="2" y="2.7" width="4" height="2.8" fill="#fff"/></svg>
        info@veltinconsulting.com
        <span class="contact-web">
          <svg viewBox="0 0 8 8"><circle cx="4" cy="4" r="4" fill="#5f7f9f"/><circle cx="4" cy="4" r="2" fill="none" stroke="#fff" stroke-width="0.8"/></svg>
          veltinconsulting.com
        </span>
      </div>
    </address>
    <div class="watermark" role="img" aria-label="Faint grey watermark of a dancer in a flowing dress"></div>
    <svg class="footer-bands" viewBox="0 0 520 16" preserveAspectRatio="none">
      <rect x="0" y="0" width="104" height="3" fill="var(--brand-gold)"/>
      <rect x="112" y="0" width="176" height="3" fill="var(--brand-blue)"/>
      <rect x="300" y="0" width="220" height="3" fill="var(--brand-gold)"/>
      <rect x="0" y="7" width="322" height="9" fill="var(--brand-blue)"/>
      <rect x="322" y="7" width="198" height="9" fill="var(--brand-gold)"/>
    </svg>
  </main>
</body>
</html>
```